Bright Harbor website redesign

We need a redesign for a website: mybrightharbor.example.

I already created a video going over what exactly is needed in the design.

See Video here: https://files.example.net/file/d/7xQpL2mR9vTz4KwB8nYcH3jDs6FgA1eU0/view?usp=sharing

SearchRate Slide shown in Video: https://slides.example.net/presentation/d/9KP_Rtnwq3XbzmLeYc7VhJ2GoUd4Fs_PaiTe6q1kQ5Wr/edit?usp=sharing

Holidays in India so we did not get enough design entries or quality.

Target Market(s)

Dentistry

Industry/Entity Type

Dentistry

Number of Pages Required

1 page

Colors
0094D4
00A9DD
6FCCEA
C7EBF8
E9F6FB
00AB8E
00BBA5
67D7C9
C6EFE9
E9F9F6

Requirements
Must have
• See 13 min video link in description - shows what to do.

```html
<!DOCTYPE html>
<html lang="en">
<head>
<meta charset="utf-8">
<title>Bright Harbor Dental</title>
<link href="https://fonts.googleapis.com/css2?family=Roboto:wght@400;500;700&family=Tinos:wght@400;700&display=swap" rel="stylesheet">
<style>
:root{
  --blue:#0094D4;
  --blue-2:#00A9DD;
  --blue-3:#6FCCEA;
  --blue-4:#C7EBF8;
  --blue-5:#E9F6FB;
  --green:#00AB8E;
  --green-2:#00BBA5;
  --green-3:#67D7C9;
  --ink:#222;
  --muted:#555;
  --red:#d8262e;
  --soft:#f6f6f6;
  --footer:#1e1e1e;
}
*{box-sizing:border-box;margin:0;padding:0}
html,body{width:1200px;height:4234px;overflow:hidden;background:#fff}
body{position:relative;font-family:"Roboto",Arial,sans-serif;color:var(--ink)}
.serif{font-family:"Tinos","Times New Roman",serif;font-weight:400}

/* header */
.site-header{position:absolute;left:0;top:0;width:1200px;height:102px;background:#fff}
.brand{position:absolute;left:99px;top:26px;font-family:"Tinos",serif;font-size:34px;color:var(--green);letter-spacing:1px}
.brand-dot{position:absolute;left:300px;top:14px;width:14px;height:14px;border-radius:50%;background:var(--red)}
.phone{position:absolute;left:635px;top:21px;font-size:15px;color:#333;display:flex;align-items:center;gap:7px}
.btn-pill{position:absolute;border-radius:20px;color:#fff;font-size:14px;font-weight:500;display:flex;align-items:center;justify-content:center}
.btn-schedule{left:784px;top:12px;width:166px;height:38px;background:var(--blue)}
.btn-emergency{left:962px;top:12px;width:136px;height:38px;background:var(--green)}
.nav a{position:absolute;top:70px;font-size:15px;color:#222;text-decoration:none}

/* hero */
.hero{position:absolute;left:0;top:102px;width:1200px;height:640px;background:linear-gradient(180deg,#1aa5df 0%,#0f8fcc 70%,#0c7fba 100%)}
.hero-photo{position:absolute;left:560px;top:160px;width:600px;height:470px;background:radial-gradient(ellipse at 55% 55%,#e9f2f7 0%,#b9d8e8 35%,rgba(20,150,210,0) 70%)}
.hero-title{position:absolute;left:112px;top:272px;font-size:59px;line-height:64px;color:#fff}
.hero-sub{position:absolute;left:112px;top:421px;font-size:17px;font-weight:500;color:#fff}
.hero-btn{position:absolute;left:110px;top:470px;width:217px;height:43px;border-radius:22px;background:#fff;color:var(--blue);font-size:15px;font-weight:500;display:flex;align-items:center;justify-content:center}
.hero-arrow{position:absolute;top:400px}
.hero-curve{position:absolute;left:0;top:600px}
.dots{position:absolute;top:684px;left:555px;display:flex;gap:13px}
.dots span{width:12px;height:12px;border-radius:50%;border:1.5px solid #fff}
.dots span.on{background:#fff}

/* section headings */
.section-title{position:absolute;left:0;width:1200px;text-align:center;font-size:36px;color:#222}

/* team */
.member{position:absolute;top:937px;width:330px;text-align:center}
.member-photo{width:165px;height:200px;margin:0 auto;border-radius:0 0 82px 82px;position:relative;overflow:hidden}
.member-photo::before{content:"";position:absolute;left:0;top:35px;width:165px;height:165px;border-radius:50%;border:3px solid var(--red);border-color:var(--red) var(--red) transparent var(--red);background:#eaeaea}
.member-photo i{position:absolute;left:30px;top:0;width:105px;height:200px;border-radius:52px 52px 0 0;background:linear-gradient(180deg,#cbb6a6 0%,#8a6f60 45%,#3c3c44 100%)}
.member-name{margin-top:26px;font-size:19px;font-weight:500}
.member-role{margin-top:8px;font-size:15px;color:#444}
.member-bio{margin-top:8px;font-size:12.5px;line-height:24px;color:#444}
.learn{display:inline-block;margin-top:7px;font-size:14px;color:var(--blue);text-decoration:underline}

/* services */
.services{position:absolute;left:0;top:1409px;width:1200px;height:593px;background:var(--soft)}
.service{position:absolute;width:170px;text-align:center}
.service-icon{width:108px;height:108px;margin:0 auto;border-radius:50%;background:#fff;box-shadow:0 3px 8px rgba(0,0,0,.10);display:flex;align-items:center;justify-content:center}
.service-icon span{width:56px;height:56px;border-radius:50%;border:2.5px solid var(--blue);background:var(--blue-5)}
.service-label{margin-top:16px;font-size:16px;font-weight:500;color:#222}

/* reviews */
.rating{position:absolute;left:306px;top:2158px;font-size:14px;font-weight:500;color:#333}
.stars{color:#f2b01e;letter-spacing:1px}
.platform{position:absolute;top:2167px;font-size:26px;font-weight:500}
.card{position:absolute;top:2257px;width:312px;height:354px;background:#fff;box-shadow:0 2px 10px rgba(0,0,0,.12)}
.card-avatar{position:absolute;left:20px;top:26px;width:54px;height:54px;border-radius:50%;background:#777}
.card-stars{position:absolute;left:86px;top:20px;font-size:20px}
.card-name{position:absolute;left:86px;top:55px;font-size:20px;font-weight:700}
.card-text{position:absolute;left:20px;top:98px;width:278px;font-size:13px;line-height:25px;color:#444}
.card-text u{color:var(--blue)}
.card-date{position:absolute;left:20px;top:263px;font-size:13.5px;color:#333}
.card-foot{position:absolute;left:0;top:298px;width:312px;height:56px;border-top:1px solid #eee;padding:0 20px;display:flex;align-items:center;justify-content:space-between;font-size:12.5px;color:#333}
.card-foot b{color:var(--red);font-size:17px;font-weight:700}
.side-arrow{position:absolute;top:2417px}

/* experience */
.exp-photo{position:absolute;left:105px;top:2788px;width:507px;height:539px;background:linear-gradient(135deg,#e9ecef 0%,#c8d2d8 40%,#9fb9c9 75%,#6fa3c4 100%)}
.exp-card{position:absolute;left:567px;top:2839px;width:526px;height:437px;background:#fff;box-shadow:0 2px 14px rgba(0,0,0,.10);padding:34px 24px 0 24px}
.exp-card h2{font-size:38px;line-height:40px;color:#222}
.exp-card p{font-size:12.5px;line-height:25px;color:#555}
.exp-card .lead{margin-top:16px}
.btn-green{display:flex;align-items:center;justify-content:center;width:156px;height:41px;border-radius:21px;background:var(--green);color:#fff;font-size:14px;font-weight:500;margin-top:22px}

/* band */
.band{position:absolute;left:0;top:3406px;width:1200px;height:426px;background:linear-gradient(180deg,#1a9ed8,#0f90cc)}
.band-title{position:absolute;left:0;top:3478px;width:1200px;text-align:center;font-size:33px;color:#fff}
.band-sub{position:absolute;left:0;top:3531px;width:1200px;text-align:center;font-size:24px;color:#fff}
.band-avatar{position:absolute;left:196px;top:3587px;width:163px;height:163px;border-radius:50%;border:3px solid #fff;background:linear-gradient(180deg,#d7c3b3,#6b5a52)}
.band-quote{position:absolute;left:378px;top:3596px;width:620px;color:#fff}
.band-quote h3{font-size:16px;font-weight:700}
.band-quote p{margin-top:9px;font-size:13px;line-height:25px}
.partners{position:absolute;left:380px;top:3716px;display:flex;gap:36px;color:#fff;font-size:16px;font-weight:500}
.partners span{display:flex;align-items:center;gap:7px}
.partners i{width:14px;height:14px;border-radius:50%;background:#fff;display:inline-block}
.band-btn{position:absolute;left:784px;top:3707px;width:219px;height:43px;border-radius:22px;background:#fff;color:#222;font-size:14.5px;font-weight:500;display:flex;align-items:center;justify-content:center}

/* footer */
.footer{position:absolute;left:0;top:3832px;width:1200px;height:402px;background:var(--footer);color:#fff}
.f-head{position:absolute;top:76px;font-size:20px}
.f-input{position:absolute;left:99px;width:266px;height:38px;background:#fff;border:1px solid #ccc;color:#888;font-size:13px;padding:10px 7px}
.f-btn{position:absolute;left:99px;top:240px;width:266px;height:40px;background:var(--blue);color:#fff;font-size:14px;font-weight:500;display:flex;align-items:center;justify-content:center}
.f-list{position:absolute;font-size:13px;line-height:33px}
.f-social{position:absolute;left:603px;top:279px;display:flex;gap:9px}
.f-social span{width:36px;height:36px;border-radius:50%;border:1.5px solid #fff}
.f-map{position:absolute;left:850px;top:104px;width:250px;height:169px;background:linear-gradient(135deg,#eef0f2,#dfe5ea 50%,#e9eef0)}
.f-rule{position:absolute;left:99px;top:339px;width:1000px;height:1px;background:#3a3a3a}
.f-copy{position:absolute;left:0;top:357px;width:1200px;text-align:center;font-size:13px}
</style>
</head>
<body>

<header class="site-header">
  <div class="brand">Bright Harbor</div>
  <div class="brand-dot"></div>
  <div class="phone">
    <svg width="15" height="15" viewBox="0 0 24 24"><path d="M6.6 10.8a15.1 15.1 0 0 0 6.6 6.6l2.2-2.2a1 1 0 0 1 1-.25 11.4 11.4 0 0 0 3.6.57 1 1 0 0 1 1 1V20a1 1 0 0 1-1 1A17 17 0 0 1 3 4a1 1 0 0 1 1-1h3.5a1 1 0 0 1 1 1c0 1.25.2 2.45.57 3.57a1 1 0 0 1-.25 1z" fill="#d8262e"/></svg>
    (555) 014-2290
  </div>
  <div class="btn-pill btn-schedule">Schedule Online</div>
  <div class="btn-pill btn-emergency">Emergency</div>
  <nav class="nav">
    <a style="left:385px">Services</a>
    <a style="left:493px">Financing</a>
    <a style="left:611px">Testimonial</a>
    <a style="left:743px">New Patient Visit</a>
    <a style="left:912px">Specials</a>
    <a style="left:1021px">Contact Us</a>
  </nav>
</header>

<section class="hero"></section>
<div class="hero-photo" role="img" aria-label="Dental tools, floss box and a large model tooth on a blue surface"></div>
<h1 class="hero-title serif">Creating Healthier<br>Smiles</h1>
<p class="hero-sub">With Advanced Technology and Affordable Treatment</p>
<div class="hero-btn">Book an Appointment</div>
<svg class="hero-arrow" style="left:66px" width="18" height="34" viewBox="0 0 18 34"><path d="M16 2 2 17l14 15" fill="none" stroke="#fff" stroke-width="1.6"/></svg>
<svg class="hero-arrow" style="left:1116px" width="18" height="34" viewBox="0 0 18 34"><path d="M2 2l14 15L2 32" fill="none" stroke="#fff" stroke-width="1.6"/></svg>
<svg class="hero-curve" width="1200" height="190" viewBox="0 0 1200 190">
  <path d="M0 40 Q600 215 1200 22 L1200 190 L0 190Z" fill="#fff"/>
  <path d="M0 36 Q600 230 1200 26 Q600 196 0 52Z" fill="var(--green)"/>
</svg>
<div class="dots"><span></span><span class="on"></span><span></span><span></span></div>

<h2 class="section-title serif" style="top:867px">Meet Our Team</h2>

<div class="member" style="left:88px">
  <div class="member-photo" role="img" aria-label="Portrait of Dr. Anika Rao"><i></i></div>
  <div class="member-name">Dr. Anika Rao, DDS</div>
  <div class="member-role">Cosmetic Dentist</div>
  <p class="member-bio">Dr. Rao is a graduate of the School of Dental Medicine at Westfield University, Ridgeton, where she studied Cosmetic Dentistry,...</p>
  <a class="learn">Learn More »</a>
</div>
<div class="member" style="left:435px">
  <div class="member-photo" role="img" aria-label="Portrait of Dr. Priya Menon"><i></i></div>
  <div class="member-name">Dr. Priya Menon, DDS</div>
  <div class="member-role">Endodontist</div>
  <p class="member-bio">Dr. Menon received her specialty training in Endodontics from Pinecrest University. She graduated with a Master of Science in dentistry degree...</p>
  <a class="learn">Learn More »</a>
</div>
<div class="member" style="left:782px">
  <div class="member-photo" role="img" aria-label="Portrait of Dr. Vikram Desai"><i></i></div>
  <div class="member-name">Dr. Vikram Desai, DDS</div>
  <div class="member-role">General Dentist</div>
  <p class="member-bio">Dr. Vikram Desai, DDS received his Bachelor of Dental Surgery Degree in 1999 from India. In 2000, he immigrated to the United States....</p>
  <a class="learn">Learn More »</a>
</div>

<section class="services">
  <h2 class="section-title serif" style="top:86px">Our Services</h2>
  <div class="service" style="left:75px;top:169px"><div class="service-icon"><span></span></div><div class="service-label">Dental Implants</div></div>
  <div class="service" style="left:250px;top:169px"><div class="service-icon"><span></span></div><div class="service-label">Cosmetic Dentistry</div></div>
  <div class="service" style="left:425px;top:169px"><div class="service-icon"><span></span></div><div class="service-label">Braces</div></div>
  <div class="service" style="left:601px;top:169px"><div class="service-icon"><span></span></div><div class="service-label">Crowns</div></div>
  <div class="service" style="left:775px;top:169px"><div class="service-icon"><span></span></div><div class="service-label">Bridge</div></div>
  <div class="service" style="left:951px;top:169px"><div class="service-icon"><span></span></div><div class="service-label">Extractions</div></div>
  <div class="service" style="left:75px;top:357px"><div class="service-icon"><span></span></div><div class="service-label">Gum Disease</div></div>
  <div class="service" style="left:250px;top:357px"><div class="service-icon"><span></span></div><div class="service-label">Root Canal</div></div>
  <div class="service" style="left:425px;top:357px"><div class="service-icon"><span></span></div><div class="service-label">Dentures</div></div>
  <div class="service" style="left:601px;top:357px"><div class="service-icon"><span></span></div><div class="service-label">Emergency Dentistry</div></div>
  <div class="service" style="left:775px;top:357px"><div class="service-icon"><span></span></div><div class="service-label">Veneers</div></div>
  <div class="service" style="left:951px;top:357px"><div class="service-icon"><span></span></div><div class="service-label">Clear Aligners</div></div>
</section>

<h2 class="section-title serif" style="top:2088px">What Our Patients Say About Us</h2>
<div class="rating">
  AVERAGE RATING<br>
  <span class="stars" style="font-size:19px">★★★★★</span> <span style="font-weight:700">4.5</span><br>
  <span style="font-weight:400;font-size:13px;margin-left:3px">(237 Reviews)</span>
</div>
<div class="platform" style="left:493px;color:var(--red)">ReviewHub</div>
<div class="platform" style="left:636px;color:#4a76c9">SearchRate</div>
<div class="platform" style="left:790px;color:#3b5a9a">FriendBook</div>

<svg class="side-arrow" style="left:68px" width="16" height="34" viewBox="0 0 16 34"><path d="M14 2 2 17l12 15" fill="none" stroke="#333" stroke-width="1.6"/></svg>
<svg class="side-arrow" style="left:1112px" width="16" height="34" viewBox="0 0 16 34"><path d="M2 2l12 15L2 32" fill="none" stroke="#333" stroke-width="1.6"/></svg>

<article class="card" style="left:100px">
  <div class="card-avatar" style="background:#fff;border:3px solid #333"></div>
  <div class="card-stars stars">★★★★★</div>
  <div class="card-name">Dana M.</div>
  <p class="card-text">I have never been an easy patient. Everything terrifies me. I have had SUCH a great experience with Bright Harbor... Valerie in particular has especially been kind and helpful. From the very first time I walked into ... <u>more</u></p>
  <div class="card-date">08 October, 2021</div>
  <div class="card-foot">Source:<b>ReviewHub</b></div>
</article>
<article class="card" style="left:444px">
  <div class="card-avatar" role="img" aria-label="Reviewer avatar" style="background:#3a3530"></div>
  <div class="card-stars stars">★★★★★</div>
  <div class="card-name">Leon Y.</div>
  <p class="card-text">Went here last July 2021 for the removal of my 1 impacted wisdom tooth. Office is clean, staff are courteous. Massage chair. Wait was quick. I chose the laughing gas and local anesthesia. Procedure is done in about 1 hou ... <u>more</u></p>
  <div class="card-date">08 October, 2021</div>
  <div class="card-foot">Source:<b>ReviewHub</b></div>
</article>
<article class="card" style="left:786px">
  <div class="card-avatar" role="img" aria-label="Reviewer avatar" style="background:#6d6a55"></div>
  <div class="card-stars stars">★★★★★</div>
  <div class="card-name">Marco P.</div>
  <p class="card-text">As most of us know going to the dentist isn't our favorite thing. But at this dental office the entire staff is super friendly, efficient, and professional. They actually start your appointment when it is scheduled, unli... <u>more</u></p>
  <div class="card-date">08 October, 2021</div>
  <div class="card-foot">Source:<b>ReviewHub</b></div>
</article>

<div class="exp-photo" role="img" aria-label="Smiling patient in a dental chair with a dentist holding a mirror"></div>
<div class="exp-card">
  <h2 class="serif">Experience the Bright Harbor Difference</h2>
  <p class="lead">Your smile is our #1 priority. At Bright Harbor, we provide affordable and expert dental solutions. Whether you are looking for a family dentist or have any emergency such as needing a root canal in Lakemont, we are here for you! We want to keep your teeth healthy inside and out. We don't just clean teeth and send you on your way, we want to get to know you.</p>
  <p>We accept most HMO and PPO insurances. We offer various financing options through FlexCare Credit, PayLater Club and In-House Plans.</p>
  <p>To constantly strive to achieve the highest level of skills and modern techniques and equipment so we can provide our patients with the best</p>
  <div class="btn-green">Learn More</div>
</div>

<section class="band" role="img" aria-label="Faint photo of a dental treatment under a blue tint"></section>
<h2 class="band-title serif">Committed to excellence in Oral Health Care</h2>
<p class="band-sub">Free Exam and X-Rays for New Patients</p>
<div class="band-avatar" role="img" aria-label="Portrait of a smiling patient"></div>
<div class="band-quote">
  <h3>De Finibus Bonorum et Malorum</h3>
  <p>Lorem ipsum dolor sit amet, consectetur adipiscing elit, sed do eiusmod tempor incididunt ut labore et dolore magna aliqua. Quis ipsum suspendisse ultrices gravida. Risus commodo viverra maecenas accumsan lacus vel facilisis.</p>
</div>
<div class="partners">
  <span><i></i>Nordline</span>
  <span><i></i>Mailcrest</span>
  <span><i></i>Outpost</span>
</div>
<div class="band-btn">Book an Appointment</div>

<footer class="footer">
  <div class="f-head serif" style="left:101px">Get In Touch</div>
  <div class="f-input" style="top:104px">Name</div>
  <div class="f-input" style="top:150px">Address</div>
  <div class="f-input" style="top:196px">Phone</div>
  <div class="f-btn">Book Your Free Consultation</div>

  <div class="f-head serif" style="left:416px">Office Hours:</div>
  <div class="f-list" style="left:414px;top:98px">
    Monday 10AM–7PM<br>Tuesday 10AM–7PM<br>Wednesday 9AM–6PM<br>Thursday 9AM–6PM<br>Friday 9AM–5PM<br>Saturday 9AM–1PM
  </div>

  <div class="f-head serif" style="left:605px">Bright Harbor</div>
  <div class="f-list" style="left:604px;top:104px;line-height:27px">
    48 Harbor View Ave., Suite A<br>Lakemont, CA 90000
  </div>
  <div class="f-list" style="left:604px;top:167px">Call Us: (555) 014-2290<br>hello@mybrightharbor.example</div>
  <div class="f-head serif" style="left:605px;top:242px">Follow Us</div>
  <div class="f-social"><span></span><span></span><span></span><span></span></div>

  <div class="f-head serif" style="left:851px">Map &amp; Directions</div>
  <div class="f-map" role="img" aria-label="Street map showing the office location"></div>

  <div class="f-rule"></div>
  <div class="f-copy">2021 Mybrightharbor . All Rights Reserved.</div>
</footer>

</body>
</html>
```